Linear Villas Andalus listings flyer

Linear Villas Andalus are a specialist estate agency focussed solely on selling modern and contemporary homes.

We need an A4 folded flyer to be designed so that Linear Villas Andalus can leaflet drop all of the modern homes for sale in our area to generate new instructions / listings. We need to engage with owners of those types of homes by posting this marketing material through their letter boxes in the hope that they see our funky and modern design and decide to call us about our services to sell their home, if for sale.

We would like to see sharp lines and a modern design (see our logo for style and colour scheme), with lots of white spaces and using photos which can blend in to the background to provide a powerful and impacting image to set us aside from any other direct mail leaflets which may be in their post box. It needs to show

* Quality
* Style
* Modern and forward thinking in design and outlook
* Professionalism

Front page
Top:
Logo of Linear Villas Andalus.
Helping you sell your modern home. It’s all we do!

4 property photos in a grid position

Bottom banner
If you are thinking of selling, read on…

INSIDE LEFT & RIGHT (DOUBLE PAGE POSSIBLY BLANK WHITE BACKGROUND)
Title: Use Linear Villas Andalus – the specialist modern homes agency to sell your home

We bring an exciting and dynamic mix of modern marketing with good old fashioned service to guarantee only the most qualified clients will be viewing your home (use online marketing image)

Marketing packages include stylish online brochures, professional photography, stunning drone video footage, informative video walk thru’s and unique floor plans (use drone and floor plan images)

Targeted social media campaigns focusing on international clientele actively looking to buy property in southern Spain (use social media image)

Bespoke, powerful advertising packages enable worldwide exposure for both online and traditional channels to market. We can be as discreet or as visible as you want us to be to sell your home

During our 20 years on the Costa del Sol, we have built up an enviable network of collaborating agents meaning you only have to instruct one expert real estate agent, Linear Villas Andalus, to gain maximum exposure for your home

BACK PAGE

If you want service that matches the value of your home, contact us today for a private, personalised consultation. Linear Villas Andalus. It’s all we do.

Suite 14
Corvena Business Centre
Avenida Los Almendros
Corvena, Marbella

Tel: +34 952 618 304
Mobil y Whatsapp: +34 677 482 051
Email: info@linearvillasandalus-example.com
www.linearvillasandalus-example.com

Target Market(s)

Wealthy property owners of contemporary and modern homes who are looking to sell their home

Industry/Entity Type

Real Estate Agent

Font styles to use
Serif
Sans Serif

Colors
606060
e7e7e7
f5f5f5

Requirements
Must have
• Classy, professional, modern design with the ability to stand out from other leaflet drops / direct mail in letter box
Nice to have
• straight lines to border photos
• Maybe extend the lines further than they should so it has the look of an architects plan
• Blend in images to white background in the middle open double page
Should not have
• Lots of different colours

```html
<!DOCTYPE html>
<html lang="en">
<head>
<meta charset="utf-8">
<title>Linear Villas Andalus – Seller Flyer</title>
<link href="https://fonts.googleapis.com/css2?family=Ubuntu:wght@300;400;500;700&display=swap" rel="stylesheet">
<style>
  :root {
    --ink: #606060;
    --ink-soft: #7a7a7a;
    --rule: #e7e7e7;
    --paper: #ffffff;
    --paper-tint: #f5f5f5;
    --stage: #d4d4d8;
  }
  * { box-sizing: border-box; margin: 0; padding: 0; }
  html, body { width: 1200px; height: 900px; overflow: hidden; }
  body {
    background: var(--stage);
    font-family: "Ubuntu", sans-serif;
    color: var(--ink);
    display: flex;
    align-items: center;
    justify-content: center;
    gap: 48px;
  }
  .panel {
    width: 370px;
    height: 780px;
    background: var(--paper);
    position: relative;
    box-shadow: 0 10px 30px rgba(0,0,0,0.12);
  }

  /* Back panel */
  .back-panel {
    display: flex;
    flex-direction: column;
    align-items: center;
    justify-content: center;
    text-align: center;
    padding: 0 40px;
  }
  .back-message {
    font-size: 13px;
    font-weight: 300;
    line-height: 1.6;
    color: var(--ink-soft);
  }
  .back-tagline {
    margin-top: 6px;
    font-size: 16px;
    font-weight: 500;
    color: var(--ink);
  }
  .brand {
    display: flex;
    align-items: center;
    gap: 8px;
    font-size: 13px;
    font-weight: 500;
    letter-spacing: 0.08em;
    text-transform: uppercase;
    color: var(--ink);
  }
  .brand-mark {
    width: 12px;
    height: 12px;
    background: var(--ink);
  }
  .back-panel .brand { margin: 34px 0 18px; }
  .address, .contacts {
    font-size: 12px;
    font-weight: 300;
    line-height: 1.6;
    color: var(--ink-soft);
    font-style: normal;
  }
  .contacts { margin-top: 16px; }

  /* Front panel */
  .front-panel .brand {
    position: absolute;
    top: 34px;
    right: 26px;
    font-size: 11px;
  }
  .photo-collage {
    position: absolute;
    top: 0;
    left: 0;
    width: 370px;
    height: 780px;
  }
  .front-cta {
    position: absolute;
    right: 26px;
    bottom: 40px;
    text-align: right;
  }
  .front-cta-lead {
    font-size: 14px;
    font-weight: 300;
    color: var(--ink-soft);
  }
  .front-cta-main {
    font-size: 24px;
    font-weight: 700;
    color: var(--ink);
    margin-top: 2px;
  }
</style>
</head>
<body>

  <section class="panel back-panel" aria-label="Back page">
    <p class="back-message">If you want service that matches the value of your home, contact us today for a private, personalised consultation. Linear Villas Andalus.</p>
    <p class="back-tagline">It’s all we do.</p>

    <div class="brand"><span class="brand-mark"></span>Linear Villas Andalus</div>

    <address class="address">
      Suite 14<br>
      Corvena Business Centre<br>
      Avenida Los Almendros<br>
      Corvena, Marbella
    </address>

    <p class="contacts">
      Tel: +34 952 618 304<br>
      Mobil y Whatsapp: +34 677 482 051<br>
      Email: info@linearvillasandalus-example.com<br>
      www.linearvillasandalus-example.com
    </p>
  </section>

  <section class="panel front-panel" aria-label="Front page">
    <div class="brand"><span class="brand-mark"></span>Linear Villas Andalus</div>

    <svg class="photo-collage" viewBox="0 0 370 780" xmlns="http://www.w3.org/2000/svg">
      <defs>
        <linearGradient id="tone-warm" x1="0" y1="0" x2="0" y2="1">
          <stop offset="0" stop-color="#8a6a4e"/>
          <stop offset="0.6" stop-color="#c48a52"/>
          <stop offset="1" stop-color="#4f5a3a"/>
        </linearGradient>
        <linearGradient id="tone-dusk" x1="0" y1="0" x2="1" y2="1">
          <stop offset="0" stop-color="#2a3446"/>
          <stop offset="0.5" stop-color="#6b6a5e"/>
          <stop offset="1" stop-color="#1f2a38"/>
        </linearGradient>
        <linearGradient id="tone-sky" x1="0" y1="0" x2="0" y2="1">
          <stop offset="0" stop-color="#3d7fd0"/>
          <stop offset="0.45" stop-color="#e9eef2"/>
          <stop offset="1" stop-color="#5a7f94"/>
        </linearGradient>
        <linearGradient id="tone-pool" x1="0" y1="0" x2="0" y2="1">
          <stop offset="0" stop-color="#2f7fc8"/>
          <stop offset="0.5" stop-color="#eef1f2"/>
          <stop offset="1" stop-color="#38b4d8"/>
        </linearGradient>
      </defs>

      <polygon role="img" aria-label="Photo: modern villa with curved glass balconies at dusk"
        fill="url(#tone-warm)" points="20,95 200,95 245,192 200,290 20,290 -25,192"/>
      <polygon role="img" aria-label="Photo: contemporary house lit up at night"
        fill="url(#tone-dusk)" points="182,238 325,238 370,345 325,452 182,452 137,345"/>
      <polygon role="img" aria-label="Photo: white modern villa with palm tree under blue sky"
        fill="url(#tone-sky)" points="0,302 98,302 128,392 98,482 0,482"/>
      <polygon role="img" aria-label="Photo: villa with swimming pool in sunshine"
        fill="url(#tone-pool)" points="100,498 272,498 314,584 272,670 100,670 58,584"/>
    </svg>

    <div class="front-cta">
      <p class="front-cta-lead">If you are thinking of selling,</p>
      <p class="front-cta-main">Read on...</p>
    </div>
  </section>

</body>
</html>
```